** Wanted ** Wordpress web design for scaffolding rental and construction company

We need a website design and must be functional to show a basic overview of what our company offers as a service. We have a domain name and a logo but we need web design. This web site should have another scaffolding rental page for construction and renovation as well as a quote section where customers can enter their personal information and also upload photos. The site% 26quot; www.brindlework.com% 26quot; should be intuitive, clear and classy ... The logo must be found on the site in several ways.

Target Market(s)

Professional and no professional

Coding

Coded - Design and coding required

Number of Pages Required

3 page

Font styles to use
Serif
Sans Serif
Decorative
Script

Requirements
Must have
• Our logo
Nice to have
• Slogan:% 26quot; The height% 26 # 224; port% 26 # 233; e hand% 26quot;

```html
<!DOCTYPE html>
<html lang="en">
<head>
<meta charset="utf-8">
<title>Brindlework — Scaffolding Rental &amp; Construction</title>
<link href="https://fonts.googleapis.com/css2?family=Michroma&family=Montserrat:ital,wght@0,400;0,500;0,600;0,700;1,400&display=swap" rel="stylesheet">
<style>
:root{
  --blue:#1a9fe0;
  --blue-deep:#0f86c6;
  --ink:#151515;
  --muted:#7a7a7a;
  --light:#f4f6f8;
  --white:#ffffff;
  --footer:#121820;
}
*{box-sizing:border-box;margin:0;padding:0}
html,body{width:1200px;height:4736px;overflow:hidden}
body{font-family:"Montserrat",Arial,sans-serif;color:var(--ink);background:var(--white);position:relative}
.abs{position:absolute}
.display{font-family:"Michroma","Montserrat",sans-serif;font-weight:400;letter-spacing:1px}
.btn{position:absolute;display:flex;align-items:center;justify-content:center;font-weight:600;font-size:16px;color:var(--white);text-decoration:none;border-radius:2px}
.btn-solid{background:var(--blue)}
.btn-ghost{border:2px solid var(--white)}
.mark{display:block;width:20px;height:20px;background:var(--blue);transform:rotate(45deg)}
.mark.white{background:var(--white)}

/* header */
.site-header{position:absolute;left:0;top:0;width:1200px;height:97px;background:var(--white)}
.brand{position:absolute;display:flex;align-items:center;gap:10px;font-family:"Michroma",sans-serif;font-size:16px;color:var(--blue);letter-spacing:1px}
.brand .sq{width:22px;height:22px;background:var(--blue)}
.main-nav a{position:absolute;top:38px;font-size:16px;color:#333;text-decoration:none}
.main-nav a.active{color:var(--blue)}
.search{position:absolute;left:978px;top:38px}
.login{position:absolute;left:1044px;top:0;width:156px;height:97px;background:var(--blue);color:var(--white);display:flex;align-items:center;justify-content:center;font-size:17px}

/* hero */
.hero{position:absolute;left:0;top:97px;width:1200px;height:555px}
.hero-photo{position:absolute;inset:0;background:linear-gradient(100deg,#2a2622 0%,#5a4635 30%,#8a7a6a 55%,#6a6e75 75%,#9aa0a8 100%)}
.hero-title{left:88px;top:122px;font-size:54px;color:var(--white)}
.hero-sub{left:90px;top:194px;width:600px;font-size:22px;line-height:28px;color:var(--white);font-weight:500}
.quote{position:absolute;left:707px;top:79px;width:335px;height:386px;background:#0b0b0b;box-shadow:8px 9px 0 var(--blue)}
.quote h2{position:absolute;left:0;top:14px;width:100%;text-align:center;font-size:22px;color:var(--white)}
.quote .mark{position:absolute;left:158px;top:64px;width:16px;height:16px}
.field{position:absolute;left:32px;width:270px;height:37px;border:1px solid #555;color:var(--white);font-size:14px;display:flex;align-items:center;justify-content:space-between;padding:0 14px 0 16px}
.field span{font-size:11px;color:#888;letter-spacing:.5px}
.field.empty{justify-content:flex-end}
.upload{position:absolute;left:32px;top:272px;width:270px;height:80px;border:1px solid #555;display:flex;flex-direction:column;align-items:center;justify-content:flex-end;padding-bottom:14px;gap:8px;font-size:11px;color:#888}
.quote .submit{left:32px;top:362px;width:270px;height:45px;font-size:17px}

/* section titles */
.sec-title{position:absolute;left:0;width:1200px;text-align:center;font-size:42px;color:var(--ink)}
.sec-title b{color:var(--blue);font-weight:400}
.sec-mark{position:absolute;left:590px}

/* why choose us */
.diamond{position:absolute;transform:rotate(45deg);background:var(--white);box-shadow:0 0 22px rgba(0,0,0,.09)}
.diamond.feature{background:var(--blue);box-shadow:none}
.why-item{position:absolute;width:300px;text-align:center}
.why-item h3{font-size:22px;font-weight:500;color:var(--blue);margin:22px 0 14px}
.why-item p{font-size:13px;line-height:25px;color:var(--muted)}
.why-item.on h3,.why-item.on p{color:var(--white)}

/* services */
.service-photo{position:absolute;width:600px;height:488px}
.service-panel{position:absolute;width:600px;height:488px;background:var(--blue);color:var(--white)}
.service-panel .eyebrow{position:absolute;font-size:15px}
.service-panel h2{position:absolute;font-size:38px;line-height:42px;color:var(--white)}
.service-panel p{position:absolute;width:505px;font-size:15.5px;line-height:28px}
.service-panel .mark{position:absolute;width:18px;height:18px}

/* projects */
.projects svg{position:absolute;left:0;top:2490px}

/* about */
.about{position:absolute;left:0;top:3222px;width:1200px;height:544px;background:var(--blue);color:var(--white)}

/* testimonials */
.card{position:absolute;top:4030px;width:327px;height:248px;background:var(--white);box-shadow:0 2px 16px rgba(0,0,0,.1);text-align:center}
.avatar{position:absolute;left:113px;top:-52px;width:100px;height:100px;border-radius:50%;background:linear-gradient(#d9d2cc,#b9aca3)}
.card h4{margin-top:78px;font-size:17px;font-weight:500}
.card p{margin:18px 22px 0;font-size:13px;line-height:24.5px;color:var(--muted);font-style:italic}
.arrow{position:absolute;top:4130px}

/* footer */
.site-footer{position:absolute;left:0;top:4383px;width:1200px;height:353px;background:linear-gradient(180deg,#141b24,#0d1218);color:#d0d4d8}
.foot-links a{position:absolute;font-size:13.5px;color:#d8dce0;text-decoration:none}
.contact-line{position:absolute;left:92px;font-size:14px;display:flex;align-items:center;gap:8px}
.rule{position:absolute;left:88px;top:300px;width:1024px;height:1px;background:#2a323c}
.copy{position:absolute;left:88px;top:320px;font-size:12.5px}
.social{position:absolute;top:316px;width:26px;height:26px;border-radius:50%;background:var(--blue)}
</style>
</head>
<body>

<header class="site-header">
  <div class="brand" style="left:14px;top:36px"><span class="sq"></span>BRINDLEWORK</div>
  <nav class="main-nav">
    <a class="active" href="#" style="left:272px">Home</a>
    <a href="#" style="left:349px">About Us</a>
    <a href="#" style="left:458px">Rental Scaffolding</a>
    <a href="#" style="left:634px">What We Do</a>
    <a href="#" style="left:766px">Projects</a>
    <a href="#" style="left:860px">Contact Us</a>
  </nav>
  <svg class="search" width="18" height="18" viewBox="0 0 18 18"><circle cx="7.5" cy="7.5" r="5.5" fill="none" stroke="#333" stroke-width="2.4"/><line x1="11.5" y1="11.5" x2="16" y2="16" stroke="#333" stroke-width="2.6"/></svg>
  <a class="login" href="#">Login</a>
</header>

<section class="hero">
  <div class="hero-photo" role="img" aria-label="Worker in a hard hat in front of scaffolding at sunset"></div>
  <h1 class="abs display hero-title">BRINDLEWORK</h1>
  <p class="abs hero-sub">Lorem ipsum dolor sit amet, consectetur adipiscing elit, sed do eiusmod tempor</p>
  <a class="btn btn-solid" href="#" style="left:90px;top:278px;width:173px;height:46px">Read More</a>

  <form class="quote">
    <h2 class="display">REQUEST A QUOTE</h2>
    <i class="mark"></i>
    <div class="field" style="top:92px">Mara Lind<span>NAME</span></div>
    <div class="field" style="top:137px">maralind@<span>EMAIL ADDRESS</span></div>
    <div class="field empty" style="top:182px"><span>PHONE NO</span></div>
    <div class="field empty" style="top:227px"><span>ADDRESS</span></div>
    <div class="upload">
      <svg width="14" height="12" viewBox="0 0 14 12"><rect x="0" y="2" width="14" height="10" rx="2" fill="#888"/><rect x="4" y="0" width="6" height="3" fill="#888"/><circle cx="7" cy="7" r="2.6" fill="#0b0b0b"/></svg>
      UPLOAD PHOTOS
    </div>
    <a class="btn btn-solid submit" href="#">Get a Quote</a>
  </form>
</section>

<section class="why">
  <h2 class="sec-title display" style="top:742px">WHY <b>CHOOSE US</b></h2>
  <i class="mark sec-mark" style="top:810px"></i>

  <div class="diamond" style="left:146px;top:934px;width:247px;height:247px"></div>
  <div class="diamond" style="left:806px;top:934px;width:247px;height:247px"></div>
  <div class="diamond feature" style="left:453px;top:911px;width:294px;height:294px"></div>

  <div class="why-item" style="left:120px;top:965px">
    <svg width="54" height="54" viewBox="0 0 54 54"><circle cx="27" cy="27" r="24" fill="none" stroke="#1a9fe0" stroke-width="2"/><polygon points="27,14 30.5,23 40,23 32.5,29 35.5,38.5 27,33 18.5,38.5 21.5,29 14,23 23.5,23" fill="none" stroke="#1a9fe0" stroke-width="2" stroke-linejoin="round"/></svg>
    <h3>Trusted Platform</h3>
    <p>Lorem ipsum dolor sit amet,<br>consectetur adipiscing elit, sed do<br>eiusmod tempor</p>
  </div>
  <div class="why-item on" style="left:450px;top:965px">
    <svg width="54" height="54" viewBox="0 0 54 54"><path d="M27 5 L45 12 V26 C45 38 37 46 27 50 C17 46 9 38 9 26 V12 Z" fill="none" stroke="#fff" stroke-width="2"/><polyline points="19,27 25,33 36,21" fill="none" stroke="#fff" stroke-width="2.4"/></svg>
    <h3>Safe &amp; Secure</h3>
    <p>Lorem ipsum dolor sit amet,<br>consectetur adipiscing elit, sed<br>do eiusmod tempor</p>
  </div>
  <div class="why-item" style="left:780px;top:965px">
    <svg width="58" height="54" viewBox="0 0 58 54"><rect x="4" y="8" width="40" height="28" fill="none" stroke="#1a9fe0" stroke-width="2"/><polyline points="12,36 12,46 22,36" fill="none" stroke="#1a9fe0" stroke-width="2"/><polyline points="48,14 54,14 54,40 46,40" fill="none" stroke="#1a9fe0" stroke-width="2"/><line x1="11" y1="17" x2="37" y2="17" stroke="#1a9fe0" stroke-width="2"/><line x1="11" y1="23" x2="37" y2="23" stroke="#1a9fe0" stroke-width="2"/><line x1="11" y1="29" x2="30" y2="29" stroke="#1a9fe0" stroke-width="2"/></svg>
    <h3>Quick Assistance</h3>
    <p>Lorem ipsum dolor sit amet,<br>consectetur adipiscing elit, sed do<br>eiusmod tempor</p>
  </div>
</section>

<section class="services">
  <div class="service-photo" role="img" aria-label="Tall scaffolding against a blue-wrapped building under a clear sky" style="left:0;top:1365px;background:linear-gradient(160deg,#2e6fb8 0%,#4b8fd0 40%,#8a7d62 75%,#6d6350 100%)"></div>
  <div class="service-panel" style="left:600px;top:1365px">
    <span class="eyebrow" style="left:58px;top:62px">Our Services</span>
    <h2 class="display" style="left:58px;top:92px">SCAFFOLDING<br>RENTAL</h2>
    <i class="mark white" style="left:61px;top:190px"></i>
    <p style="left:58px;top:236px">Lorem ipsum dolor sit amet, consectetur adipiscing elit, sed do eiusmod tempor incididunt ut labore et dolore magna aliqua. Ut enim ad minim veniam, quis nostrud exercitation ullamco laboris nisi ut aliquip ex ea commodo consequat.</p>
    <a class="btn btn-ghost" href="#" style="left:58px;top:377px;width:158px;height:48px">Read More</a>
  </div>

  <div class="service-panel" style="left:0;top:1853px">
    <span class="eyebrow" style="left:40px;top:84px">Our Services</span>
    <h2 class="display" style="left:40px;top:114px">CONSTRUCTION</h2>
    <i class="mark white" style="left:45px;top:180px"></i>
    <p style="left:40px;top:221px">Lorem ipsum dolor sit amet, consectetur adipiscing elit, sed do eiusmod tempor incididunt ut labore et dolore magna aliqua. Ut enim ad minim veniam, quis nostrud exercitation ullamco laboris nisi ut aliquip ex ea commodo consequat.</p>
    <a class="btn btn-ghost" href="#" style="left:40px;top:361px;width:160px;height:48px">Read More</a>
  </div>
  <div class="service-photo" role="img" aria-label="Close view of scaffolding tubes and yellow braces along a building facade" style="left:600px;top:1853px;background:linear-gradient(135deg,#5b6066 0%,#b8bcc0 45%,#8f949a 70%,#c9b046 100%)"></div>
</section>

<section class="projects">
  <h2 class="sec-title display" style="top:2434px">PROJECTS</h2>
  <i class="mark sec-mark" style="top:2500px"></i>
  <svg width="1200" height="580" viewBox="0 2490 1200 580">
    <defs>
      <linearGradient id="tileA" x1="0" y1="0" x2="1" y2="1"><stop offset="0" stop-color="#d8dade"/><stop offset="1" stop-color="#6c7178"/></linearGradient>
      <linearGradient id="tileB" x1="0" y1="0" x2="1" y2="1"><stop offset="0" stop-color="#a88a6a"/><stop offset="1" stop-color="#5a4a3a"/></linearGradient>
      <linearGradient id="tileC" x1="0" y1="0" x2="1" y2="1"><stop offset="0" stop-color="#c4ccd4"/><stop offset="1" stop-color="#4e5a64"/></linearGradient>
      <linearGradient id="tileD" x1="0" y1="0" x2="1" y2="1"><stop offset="0" stop-color="#9c5a3c"/><stop offset="1" stop-color="#4a2c20"/></linearGradient>
      <linearGradient id="tileE" x1="0" y1="0" x2="1" y2="1"><stop offset="0" stop-color="#e0e2e0"/><stop offset="1" stop-color="#c8d040"/></linearGradient>
      <linearGradient id="tileF" x1="0" y1="0" x2="1" y2="1"><stop offset="0" stop-color="#1a9fe0"/><stop offset="1" stop-color="#0e6fa6"/></linearGradient>
    </defs>
    <polygon role="img" aria-label="Worker in a white hard hat and high-visibility vest" points="178,2642 316,2780 178,2918 40,2780" fill="url(#tileE)"/>
    <polygon role="img" aria-label="City skyline behind a construction site" points="413,2505 548,2640 413,2775 278,2640" fill="url(#tileA)"/>
    <polygon role="img" aria-label="Blue scaffolding tower beside a grey building" points="413,2785 548,2920 413,3055 278,2920" fill="url(#tileC)"/>
    <polygon role="img" aria-label="Highlighted project over a blue overlay" points="600,2600 780,2780 600,2960 420,2780" fill="url(#tileF)"/>
    <polygon role="img" aria-label="Workers in safety vests in front of a scaffolded building" points="787,2505 922,2640 787,2775 652,2640" fill="url(#tileB)"/>
    <polygon role="img" aria-label="Scaffolding along the side of a large building" points="787,2785 922,2920 787,3055 652,2920" fill="url(#tileC)"/>
    <polygon role="img" aria-label="Red scaffolding rising up a brick building" points="998,2616 1162,2780 998,2944 834,2780" fill="url(#tileD)"/>
  </svg>
  <a class="btn btn-solid" href="#" style="left:493px;top:3071px;width:213px;height:49px">View All Projects</a>
</section>

<section class="about">
  <svg class="abs" style="left:95px;top:30px" width="460" height="480" viewBox="0 0 460 480">
    <defs><linearGradient id="dusk" x1="0" y1="0" x2="0" y2="1"><stop offset="0" stop-color="#7a8fc4"/><stop offset=".55" stop-color="#f0a58a"/><stop offset="1" stop-color="#2c2f3c"/></linearGradient></defs>
    <polygon role="img" aria-label="Silhouette of a worker on scaffolding against a dusk sky" points="230,10 460,240 230,470 0,240" fill="url(#dusk)"/>
  </svg>
  <h2 class="abs display" style="left:658px;top:110px;font-size:40px;color:#fff">ABOUT US</h2>
  <i class="mark white abs" style="left:662px;top:173px;width:18px;height:18px"></i>
  <p class="abs" style="left:658px;top:220px;width:452px;font-size:15.5px;line-height:28px;text-align:justify">Lorem ipsum dolor sit amet, consectetur adipiscing elit, sed do eiusmod tempor incididunt ut labore et dolore magna aliqua. Ut enim ad minim veniam, quis nostrud exercitation ullamco laboris nisi ut aliquip ex ea commodo consequat.</p>
  <a class="btn btn-ghost" href="#" style="left:658px;top:384px;width:158px;height:49px">Read More</a>
</section>

<section class="testimonials">
  <h2 class="sec-title display" style="top:3858px">TESTIMONIALS</h2>
  <i class="mark sec-mark" style="top:3924px"></i>
  <svg class="arrow" style="left:30px" width="28" height="52" viewBox="0 0 28 52"><polyline points="24,4 4,26 24,48" fill="none" stroke="#999" stroke-width="3"/></svg>
  <svg class="arrow" style="left:1144px" width="28" height="52" viewBox="0 0 28 52"><polyline points="4,4 24,26 4,48" fill="none" stroke="#999" stroke-width="3"/></svg>

  <article class="card" style="left:88px">
    <div class="avatar" role="img" aria-label="Portrait of Mara Lind"></div>
    <h4>Mara Lind</h4>
    <p>"Lorem ipsum dolor sit amet, consectetur adipiscing elit, sed do eiusmod tempor incididunt ut labore et dolore magna aliqua. Ut enim ad minim veniam, quistrud exercitation ullamco laboris nisi"</p>
  </article>
  <article class="card" style="left:436px">
    <div class="avatar" role="img" aria-label="Portrait of Tobin Rees"></div>
    <h4>Tobin Rees</h4>
    <p>"Lorem ipsum dolor sit amet, consectetur adipiscing elit, sed do eiusmod tempor incididunt ut labore et dolore magna aliqua. Ut enim ad minim veniam, quistrud exercitation ullamco laboris nisi"</p>
  </article>
  <article class="card" style="left:783px">
    <div class="avatar" role="img" aria-label="Portrait of Ellis Ford"></div>
    <h4>Ellis Ford</h4>
    <p>"Lorem ipsum dolor sit amet, consectetur adipiscing elit, sed do eiusmod tempor incididunt ut labore et dolore magna aliqua. Ut enim ad minim veniam, quistrud exercitation ullamco laboris nisi"</p>
  </article>
</section>

<footer class="site-footer">
  <div class="brand" style="left:92px;top:72px;color:#fff;font-size:18px"><span class="sq"></span>BRINDLEWORK</div>
  <div class="contact-line" style="top:188px">
    <svg width="12" height="12" viewBox="0 0 12 12"><path d="M2 1 L4.5 1 L5.5 3.8 L4 5 C4.8 6.8 5.4 7.4 7 8 L8.2 6.5 L11 7.5 L11 10 C11 10.6 10.6 11 10 11 C5 11 1 7 1 2 C1 1.4 1.4 1 2 1 Z" fill="#d0d4d8"/></svg>+1 555 014 2290
  </div>
  <div class="contact-line" style="top:214px">
    <svg width="13" height="10" viewBox="0 0 13 10"><rect x="0" y="0" width="13" height="10" rx="1" fill="#d0d4d8"/><polyline points="0.5,0.8 6.5,5.5 12.5,0.8" fill="none" stroke="#141b24" stroke-width="1.2"/></svg>hello@brindlework.com
  </div>
  <nav class="foot-links">
    <a href="#" style="left:605px;top:58px">Home</a>
    <a href="#" style="left:605px;top:85px">About Us</a>
    <a href="#" style="left:605px;top:112px">Rental Scaffolding</a>
    <a href="#" style="left:605px;top:139px">What We Do</a>
    <a href="#" style="left:605px;top:166px">Projects</a>
    <a href="#" style="left:605px;top:193px">Contact Us</a>
    <a href="#" style="left:834px;top:58px">Faq</a>
    <a href="#" style="left:834px;top:85px">Privacy Policy</a>
    <a href="#" style="left:834px;top:112px">Terms &amp; Conditions</a>
    <a href="#" style="left:834px;top:139px">Sitemap</a>
    <a href="#" style="left:1058px;top:58px">Login</a>
    <a href="#" style="left:1058px;top:85px">Articles</a>
  </nav>
  <div class="rule"></div>
  <p class="copy">Copyrights © 2020, Brindlework. All rights reserved.</p>
  <span class="social" style="left:926px"></span>
  <span class="social" style="left:966px"></span>
  <span class="social" style="left:1006px"></span>
  <span class="social" style="left:1046px"></span>
  <span class="social" style="left:1086px"></span>
</footer>

</body>
</html>
```